Clean business card with logo provided

I want a card that will stand out among the masses. I need the color and image to show professionalism and yet have a family appeal showing that I only deal with win/win scenarios. The back of the card will be used to take notes about the individual so I can use that in my database entry. I like modern design but need professionalism in it also. It needs to fit my "clean, safe, and affordable housing" motto. I need to be able to write on the file and update the card details for my employees.

Target Market(s)

Investors looking to make investment income through real estate

Industry/Entity Type

Real Estate

Contact Information for Business Card

Brent Kovalich
blank address, city, st, zip code
480-555-3174
brentkovalich@ridgeworthrentals.example
www.ridgeworthrentals.example

Font styles to use
Sans Serif

Requirements
Must have
• I would like the back of the card to have lines for info. example
• Met/Visited: Date:
• Interets:
Nice to have
• I want the cards color to match the logo background color. Font with details to be san serif and black. I want the card rectangular with square corners. Standard business card size. I would like to see cards designed with both images to see which i prefer more.

```html
<!DOCTYPE html>
<html lang="en">
<head>
<meta charset="utf-8">
<title>Ridgeworth Rentals LLC – Business Card</title>
<link href="https://fonts.googleapis.com/css2?family=Lato:wght@400;700&family=Open+Sans:wght@400;600&display=swap" rel="stylesheet">
<style>
  :root {
    --teal: #1fb5cf;
    --teal-dark: #1597ad;
    --ink: #111111;
    --black: #0b0b0b;
    --white: #ffffff;
    --rule: #2a2a2a;
    --page: #e9e6e1;
  }
  * { box-sizing: border-box; margin: 0; padding: 0; }
  html, body {
    width: 1200px; height: 950px; overflow: hidden;
    background: var(--page);
    font-family: "Open Sans", sans-serif;
  }
  .sheet {
    width: 1200px; height: 950px;
    display: flex; flex-direction: column; align-items: center; justify-content: center;
    gap: 50px;
  }
  .card {
    position: relative; width: 700px; height: 400px; overflow: hidden;
    box-shadow: 0 6px 18px rgba(0,0,0,.18);
  }

  /* ---------- notes side ---------- */
  .card--notes { background: var(--white); }
  .notes-band {
    position: absolute; left: 0; top: 0; width: 100%; height: 170px;
    background: var(--teal);
    display: flex; flex-direction: column; align-items: center; justify-content: center;
  }
  .brand { display: flex; align-items: center; gap: 12px; }
  .brand-name {
    font-family: "Lato", sans-serif; font-weight: 700; letter-spacing: 3px;
    font-size: 34px; line-height: 1;
  }
  .brand-dot { width: 14px; height: 14px; border-radius: 50%; flex: none; }
  .card--notes .brand-name { color: var(--white); }
  .card--notes .brand-dot { background: var(--white); }
  .tagline {
    margin-top: 10px; font-family: "Lato", sans-serif; font-size: 14px;
    letter-spacing: .5px;
  }
  .card--notes .tagline { color: var(--white); }

  .notes-field {
    position: absolute; display: flex; align-items: flex-end; gap: 10px;
    font-family: "Lato", sans-serif; font-size: 17px; color: var(--teal); letter-spacing: .5px;
  }
  .notes-field .line { flex: 1; border-bottom: 1.5px solid var(--rule); height: 1px; margin-bottom: 4px; }
  .field-date { left: 470px; top: 200px; width: 200px; }
  .field-met { left: 40px; top: 250px; width: 630px; }
  .field-interests { left: 40px; top: 300px; width: 630px; }
  .field-extra { left: 40px; top: 350px; width: 630px; }

  /* ---------- contact side ---------- */
  .card--contact { background: var(--black); }
  .contact-waves { position: absolute; inset: 0; }
  .card--contact .brand { position: absolute; left: 44px; top: 72px; }
  .card--contact .brand-name { color: var(--teal); font-size: 28px; line-height: 1.15; }
  .card--contact .brand-dot { background: var(--teal); }
  .card--contact .tagline {
    position: absolute; left: 44px; top: 150px; margin: 0;
    color: var(--teal); font-size: 12px;
  }

  .contact-block {
    position: absolute; right: 30px; top: 118px; text-align: right; color: var(--ink);
  }
  .person-name {
    font-family: "Lato", sans-serif; font-size: 22px; letter-spacing: 1.5px;
    text-transform: uppercase; margin-bottom: 6px;
  }
  .contact-row {
    display: flex; justify-content: flex-end; align-items: center; gap: 8px;
    font-size: 14px; line-height: 23px;
  }
  .contact-row svg { width: 13px; height: 13px; flex: none; }
  .address {
    position: absolute; left: 40px; bottom: 28px; color: var(--ink);
    font-size: 17px; line-height: 23px;
  }
</style>
</head>
<body>
<main class="sheet">

  <section class="card card--notes" aria-label="Card notes side">
    <div class="notes-band">
      <div class="brand"><span class="brand-name">RIDGEWORTH RENTALS LLC</span><span class="brand-dot"></span></div>
      <p class="tagline">Providing clean, safe, and affordable housing</p>
    </div>
    <div class="notes-field field-date"><span>DATE:</span><span class="line"></span></div>
    <div class="notes-field field-met"><span>MET/VISITED:</span><span class="line"></span></div>
    <div class="notes-field field-interests"><span>INTERETS:</span><span class="line"></span></div>
    <div class="notes-field field-extra"><span class="line"></span></div>
  </section>

  <section class="card card--contact" aria-label="Card contact side">
    <svg class="contact-waves" viewBox="0 0 700 400" preserveAspectRatio="none" aria-hidden="true">
      <path d="M0,280 C120,310 240,300 290,225 C330,165 350,75 420,35 C510,-10 620,-8 700,-10 L700,400 L0,400 Z" fill="var(--white)"/>
      <path d="M0,300 C120,330 240,320 300,240 C340,180 360,90 430,50 C520,5 620,10 700,10 L700,400 L0,400 Z" fill="var(--teal)"/>
      <path d="M0,322 C130,352 255,342 318,258 C360,198 380,110 448,72 C535,28 625,32 700,32" fill="none" stroke="var(--teal-dark)" stroke-width="2" opacity=".45"/>
    </svg>

    <div class="brand"><span class="brand-name">RIDGEWORTH<br>RENTALS LLC</span><span class="brand-dot"></span></div>
    <p class="tagline">Providing clean, safe, and affordable housing</p>

    <div class="contact-block">
      <p class="person-name">Brent Kovalich</p>
      <p class="contact-row">480-555-3174
        <svg viewBox="0 0 24 24"><path d="M6.6 10.8a15.1 15.1 0 0 0 6.6 6.6l2.2-2.2a1 1 0 0 1 1-.25 11.4 11.4 0 0 0 3.6.57 1 1 0 0 1 1 1V20a1 1 0 0 1-1 1A17 17 0 0 1 3 4a1 1 0 0 1 1-1h3.5a1 1 0 0 1 1 1c0 1.25.2 2.45.57 3.57a1 1 0 0 1-.25 1z" fill="var(--ink)"/></svg>
      </p>
      <p class="contact-row">brentkovalich@ridgeworthrentals.example
        <svg viewBox="0 0 24 24"><rect x="2" y="5" width="20" height="14" rx="1.5" fill="var(--ink)"/><path d="M3 6l9 7 9-7" fill="none" stroke="var(--teal)" stroke-width="1.6"/></svg>
      </p>
      <p class="contact-row">www.ridgeworthrentals.example
        <svg viewBox="0 0 24 24"><circle cx="12" cy="12" r="9" fill="none" stroke="var(--ink)" stroke-width="2"/><path d="M3 12h18M12 3c3 3 3 15 0 18M12 3c-3 3-3 15 0 18" fill="none" stroke="var(--ink)" stroke-width="1.5"/></svg>
      </p>
    </div>

    <p class="address">2841 Willowbend Lane<br>Fairbanks, Alaska 99701</p>
  </section>

</main>
</body>
</html>
```